Satchel & Sundial needs new business card design

I need a new business card design. I'm looking for out-of-the-box design which represents the freedom of being a location independent entrepreneur.
I offer coaching, retreats and trips.
I would like to see designs with and without the photo.
Colors I use are black (#000000), green (#25A796) and brown (#D7C38C)
Website satchelandsundial.example

Target Market(s)

location independent entrepreneurs, digital nomads, people looking to swap the 9 to 5 for a lifestyle business

Industry/Entity Type

Business

Contact Information for Business Card

Dorota Falkner
Your Lifestyle Business Coach, Retreat & Trip Leader
http://satchelandsundial.example
hello@satchelandsundial.example
Live a life you don't need a holiday from

Font styles to use
Serif
Sans Serif

Requirements
Must have
• One side should contain only the logo. I would also consider having the "Live a life you don't need a holiday from" on that side too (depending on how it looks)
• Please show both sides on the designs.

```html
<!DOCTYPE html>
<html lang="en">
<head>
<meta charset="utf-8">
<title>Satchel &amp; Sundial – Business Card</title>
<link rel="stylesheet" href="https://fonts.googleapis.com/css2?family=Source+Sans+3:wght@400;600&display=swap">
<style>
  :root {
    --green: #25A796;
    --sand: #D7C38C;
    --ink: #000000;
    --white: #ffffff;
    --backdrop: #ecebe7;
  }
  * { margin: 0; padding: 0; box-sizing: border-box; }
  html, body {
    width: 1200px;
    height: 900px;
    overflow: hidden;
    background: var(--backdrop);
    font-family: "Source Sans 3", Arial, sans-serif;
  }
  .stage { position: relative; width: 1200px; height: 900px; }
  .card-shapes { position: absolute; inset: 0; }
  .card-shapes .front-shape { fill: var(--green); }
  .card-shapes .back-shape { fill: var(--sand); }

  .front-text { position: absolute; left: 262px; color: var(--white); white-space: nowrap; }
  .holder-name { top: 100px; font-size: 18px; font-weight: 600; }
  .holder-role { top: 134px; font-size: 15px; line-height: 20px; }
  .contact-list { top: 272px; list-style: none; font-size: 15px; line-height: 20px; }
  .contact-list li { display: flex; align-items: center; gap: 8px; }
  .contact-list svg { width: 11px; height: 11px; fill: var(--white); flex: none; }
  .tagline { top: 341px; font-size: 15px; text-transform: uppercase; letter-spacing: 0.1px; }

  .brand-name {
    position: absolute;
    right: 205px;
    top: 640px;
    font-size: 36px;
    font-weight: 600;
    color: var(--ink);
    white-space: nowrap;
  }
</style>
</head>
<body>
<main class="stage">
  <svg class="card-shapes" width="1200" height="900" viewBox="0 0 1200 900" aria-hidden="true">
    <polygon class="front-shape" points="238,62 790,62 643,235 790,405 238,405"/>
    <polygon class="back-shape" points="462,518 1018,518 1018,860 462,860 610,690"/>
  </svg>

  <section class="card-front">
    <h1 class="front-text holder-name">Dorota Falkner</h1>
    <p class="front-text holder-role">Your Lifestyle Business Coach<br>Retreat &amp; Trip Leader</p>
    <ul class="front-text contact-list">
      <li>
        <svg viewBox="0 0 12 12" aria-hidden="true"><path d="M0 2h12v8H0z M0 2l6 4.5L12 2" /><path d="M1 3l5 3.7L11 3" fill="none" stroke="#25A796" stroke-width="1"/></svg>
        hello@satchelandsundial.example
      </li>
      <li>
        <svg viewBox="0 0 12 12" aria-hidden="true"><circle cx="6" cy="6" r="6"/><path d="M2 5h8M2 7.5h8M6 0.5c-2.2 2.8-2.2 8.2 0 11M6 0.5c2.2 2.8 2.2 8.2 0 11" fill="none" stroke="#25A796" stroke-width="0.9"/></svg>
        www.satchelandsundial.example
      </li>
    </ul>
    <p class="front-text tagline">Live a life you don't need a holiday from</p>
  </section>

  <section class="card-back">
    <p class="brand-name">Satchel &amp; Sundial</p>
  </section>
</main>
</body>
</html>
```